Garlic Farm for Farm Sales/Restaurant sales

Need a professional, but appealing to agriculture world. We are selling 27 kinds of Organic Garlic from a farm in Simla,CO. I have uploaded logo and business information-we are going to need a template, because I will need to use it for four separate people.
-We are trying to appeal to Farm to table restaurants
-As well as growers/farmers

Target Market(s)

Agriculture Sales/Restaurants-Organic

Industry/Entity Type

Agriculture

Contact Information for Business Card

Want it to look more unique then your average kelto stock card- I want it to look amazing

Font styles to use
Sans Serif

Colors
0455a3
ec1f27
fbed22
ffffff

Requirements
Must have
• Just be creative
Nice to have
• Colorful
Should not have
• plain

```html
<!DOCTYPE html>
<html lang="en">
<head>
<meta charset="utf-8">
<title>Prairie Clove – Business Card</title>
<link href="https://fonts.googleapis.com/css2?family=Open+Sans:wght@400;600;700&display=swap" rel="stylesheet">
<style>
  :root {
    --navy: #1c2f6b;
    --navy-deep: #1a2a63;
    --red: #c8102e;
    --yellow: #f6c500;
    --white: #ffffff;
    --ink-grey: #5a5a5a;
    --rule-grey: #b8b8b8;
    --stage: #e9e7e3;
  }
  * { margin: 0; padding: 0; box-sizing: border-box; }
  html, body {
    width: 1200px; height: 987px; overflow: hidden;
    background: var(--stage);
    font-family: "Open Sans", Arial, sans-serif;
  }
  .canvas { position: relative; width: 1200px; height: 987px; }
  .card {
    position: absolute; left: 293px; width: 615px; height: 352px;
    box-shadow: 0 3px 8px rgba(0,0,0,.25);
    overflow: hidden;
  }
  .card--front { top: 130px; background: var(--white); }
  .card--back { top: 505px; background: var(--navy-deep); }

  .brand-mark {
    position: absolute; left: 50%; transform: translateX(-50%);
    text-align: center;
  }
  .card--front .brand-mark { top: 30px; }
  .brand-dot {
    display: block; margin: 0 auto 10px;
    width: 90px; height: 90px; border-radius: 50%;
    background: var(--red);
  }
  .brand-name {
    font-weight: 700; font-size: 38px; line-height: 1; letter-spacing: .5px;
    color: var(--navy); white-space: nowrap;
  }

  .contact-row { position: absolute; top: 250px; left: 0; right: 0; height: 50px; }
  .person { position: absolute; left: 33px; top: 2px; }
  .person-name { font-weight: 600; font-size: 20px; color: var(--navy); line-height: 24px; letter-spacing: .3px; }
  .person-role { font-size: 15px; color: var(--red); line-height: 22px; }
  .divider { position: absolute; top: 0; width: 2px; height: 50px; background: var(--rule-grey); }
  .divider--a { left: 197px; }
  .divider--b { left: 380px; }
  .address {
    position: absolute; left: 215px; width: 150px; top: 2px;
    text-align: center; font-size: 15px; line-height: 23px; color: var(--ink-grey);
  }
  .reach { position: absolute; left: 410px; top: 2px; font-size: 15px; line-height: 23px; color: var(--ink-grey); }
  .reach-line { display: flex; align-items: center; gap: 7px; }
  .reach-line svg { width: 13px; height: 13px; fill: var(--navy); }

  .footer-bands { position: absolute; left: 0; bottom: 4px; width: 615px; height: 29px; }
  .web {
    position: absolute; right: 24px; bottom: 8px;
    font-size: 15px; letter-spacing: 2.5px; font-style: italic; color: var(--white);
  }

  .pattern-field { position: absolute; inset: 0; background: radial-gradient(circle at 50% 50%, #22356e, var(--navy-deep)); }
  .card--back .brand-mark { top: 136px; }
  .card--back .brand-name { color: var(--white); font-size: 46px; }
  .social-row {
    position: absolute; top: 280px; left: 50%; transform: translateX(-50%);
    display: flex; gap: 3px;
  }
  .social-slot { width: 23px; height: 23px; border-radius: 50%; border: 2px solid var(--white); }
</style>
</head>
<body>
<main class="canvas">
  <section class="card card--front" aria-label="Business card front">
    <div class="brand-mark">
      <span class="brand-dot"></span>
      <div class="brand-name">Prairie Clove</div>
    </div>

    <div class="contact-row">
      <div class="person">
        <div class="person-name">DALE MORROW</div>
        <div class="person-role">CEO/FOUNDER</div>
      </div>
      <span class="divider divider--a"></span>
      <div class="address">P.O. Box 48 Ardell<br>CO&nbsp;&nbsp;80912</div>
      <span class="divider divider--b"></span>
      <div class="reach">
        <div class="reach-line">
          <svg viewBox="0 0 24 24"><path d="M6.6 10.8a15.1 15.1 0 0 0 6.6 6.6l2.2-2.2c.3-.3.7-.4 1-.2 1.1.4 2.3.6 3.6.6.6 0 1 .4 1 1V20c0 .6-.4 1-1 1C10.6 21 3 13.4 3 4c0-.6.4-1 1-1h3.5c.6 0 1 .4 1 1 0 1.3.2 2.5.6 3.6.1.3 0 .7-.2 1z"/></svg>
          <span>555-014-2290</span>
        </div>
        <div class="reach-line">
          <svg viewBox="0 0 24 24"><path d="M2 5h20v14H2z M2 5l10 8 10-8" fill="none" stroke="#1c2f6b" stroke-width="2.4"/><path d="M2 5h20l-10 8z"/></svg>
          <span>Nora@PCGarlic.com</span>
        </div>
      </div>
    </div>

    <svg class="footer-bands" viewBox="0 0 615 29" aria-hidden="true">
      <rect x="0" y="11" width="185" height="8" fill="var(--red)"/>
      <polygon points="183,11 375,11 372,19 180,19" fill="var(--yellow)"/>
      <path d="M372 29 L378 8 Q381 0 390 0 L615 0 L615 29 Z" fill="var(--navy)"/>
    </svg>
    <div class="web">www.PCGarlic.com</div>
  </section>

  <section class="card card--back" aria-label="Business card back">
    <div class="pattern-field" role="img" aria-label="Repeating pattern of garlic bulbs in muted teal on navy"></div>
    <div class="brand-mark">
      <div class="brand-name">Prairie Clove</div>
    </div>
    <div class="social-row" aria-label="Social media links">
      <span class="social-slot"></span>
      <span class="social-slot"></span>
      <span class="social-slot"></span>
      <span class="social-slot"></span>
    </div>
  </section>
</main>
</body>
</html>
```